IT Company requires new Business Card design.

Over the years we have had a few different business card designs. We are now due for new cards across the board for all staff. We felt this would be a good time to start fresh with a new design. Our traditional card simply had our details on the front, and a list of services on the back. We don't particularly need the list of services, we have had cards where the only thing on the rear of the card was our logo.
Feel free to be creative, we would like our tag line "Complete IT Management" to appear at some point, doesn't necessarily have to be with the logo.
I have attached samples and drafts of various previous cards we have used over the years.

```html
<!DOCTYPE html>
<html lang="en">
<head>
<meta charset="utf-8">
<title>Ridgeline Networks – Business Card</title>
<link rel="stylesheet" href="https://fonts.googleapis.com/css2?family=Roboto:wght@900&family=PT+Sans:wght@400;700&display=swap">
<style>
  :root {
    --page-bg: #ecebe8;
    --card-bg: #ffffff;
    --slate: #5e6f7d;
    --ink: #4b5661;
    --muted: #6c7680;
    --card-shadow: rgba(40, 45, 50, 0.18);
  }
  * { box-sizing: border-box; margin: 0; padding: 0; }
  html, body {
    width: 1200px; height: 720px; overflow: hidden;
    background: var(--page-bg);
  }
  .stage {
    width: 1200px; height: 720px;
    display: flex; align-items: center; justify-content: center; gap: 40px;
  }
  .card {
    position: relative;
    width: 540px; height: 309px;
    background: var(--card-bg);
    box-shadow: 0 6px 18px var(--card-shadow);
    font-family: "PT Sans", Arial, sans-serif;
    color: var(--ink);
  }
  .wordmark {
    font-family: "Roboto", Arial, sans-serif;
    font-weight: 900;
    color: var(--slate);
    line-height: 0.9;
    letter-spacing: -0.5px;
  }
  /* front */
  .card-front .wordmark { position: absolute; left: 44px; top: 40px; }
  .card-front .wordmark-top { font-size: 36px; display: block; }
  .card-front .wordmark-bottom { font-size: 25px; display: block; }
  .person { position: absolute; left: 44px; top: 122px; }
  .person-name { font-size: 17px; font-weight: 700; }
  .person-title { font-size: 14px; color: var(--muted); margin-bottom: 6px; }
  .contact-list { list-style: none; font-size: 14px; line-height: 19px; }
  .contact-list li { display: flex; align-items: center; gap: 7px; }
  .contact-list svg { width: 12px; height: 12px; fill: var(--ink); flex: none; }
  .address { font-size: 14px; line-height: 18px; margin-top: 8px; }
  .brand-square {
    position: absolute; right: 56px; top: 26px;
    width: 170px; height: 170px; background: var(--slate);
  }
  .tagline {
    position: absolute; right: 40px; top: 216px;
    font-size: 11px; letter-spacing: 3px; text-transform: uppercase; color: var(--slate);
  }
  /* back */
  .lockup {
    position: absolute; left: 0; right: 0; top: 92px;
    display: flex; align-items: center; justify-content: center; gap: 16px;
  }
  .lockup-square { width: 92px; height: 92px; background: var(--slate); }
  .card-back .wordmark-top { font-size: 44px; display: block; }
  .card-back .wordmark-bottom { font-size: 30px; display: block; }
  .web-address {
    position: absolute; right: 40px; bottom: 34px;
    font-size: 18px; letter-spacing: 1.5px; color: var(--ink);
  }
</style>
</head>
<body>
<main class="stage">
  <section class="card card-front">
    <div class="wordmark">
      <span class="wordmark-top">RIDGELINE</span>
      <span class="wordmark-bottom">NETWORKS</span>
    </div>
    <div class="person">
      <p class="person-name">Daniel Hart</p>
      <p class="person-title">Operation Manager</p>
      <ul class="contact-list">
        <li><svg viewBox="0 0 12 12"><path d="M2.5 1h2l1 3-1.3 1a6 6 0 0 0 2.8 2.8l1-1.3 3 1v2c0 .8-.7 1.5-1.5 1.5A9.5 9.5 0 0 1 1 2.5C1 1.7 1.7 1 2.5 1z"/></svg>08 5550 1234</li>
        <li><svg viewBox="0 0 12 12"><path d="M3.5 0h5c.6 0 1 .4 1 1v10c0 .6-.4 1-1 1h-5c-.6 0-1-.4-1-1V1c0-.6.4-1 1-1zm.5 1.5v7h4v-7z"/></svg>0400 555 018</li>
        <li><svg viewBox="0 0 12 12"><path d="M3 0h5v3H3zM1 4h10v5H9v3H3V9H1zm3 3v4h4V7z"/></svg>08 5550 1234</li>
        <li><svg viewBox="0 0 12 12"><path d="M0 2h12v8H0zm1 1v.4L6 7l5-3.6V3z"/></svg>daniel@ridgelinenetworks.com.au</li>
        <li><svg viewBox="0 0 12 12"><path d="M6 0a6 6 0 1 1 0 12A6 6 0 0 1 6 0zm0 1.2A4.8 4.8 0 0 0 1.3 5.4h9.4A4.8 4.8 0 0 0 6 1.2zm-4.7 5.4A4.8 4.8 0 0 0 10.7 6.6z"/></svg>www.ridgelinenetworks.com.au</li>
      </ul>
      <p class="address">Unit 4 12 Ridge Road<br>Ferndale WA 6000</p>
    </div>
    <div class="brand-square"></div>
    <p class="tagline">Complete IT Management</p>
  </section>

  <section class="card card-back">
    <div class="lockup">
      <div class="lockup-square"></div>
      <div class="wordmark">
        <span class="wordmark-top">RIDGELINE</span>
        <span class="wordmark-bottom">NETWORKS</span>
      </div>
    </div>
    <p class="web-address">www.ridgelinenetworks.com.au</p>
  </section>
</main>
</body>
</html>
```